Pelican HVAC WordPress website design

Design a new modern, clean, website for HVAC mechanical business that uses company logo/colors for branding and recognition. Files attached are just for band and color information. Here is a website design that appeals to me https://www.corvellsupply.example/

A clear description of who we are and what we do

An easily-navigated site map

An easily-navigated site map for mobile devices

Easy-to-find contact information

Obvious call to action for service, installs or to schedule estimates

about us page

Provide a way for potential customers to contact us via text or email

provide a way that allows a customer to upload a picture to request a service call or quote.
Updates

I'm looking for the design to be completed in WordPress

Industry/Entity Type

HVAC Mechanical & Building Automation / Controls contractor

Coding

Coded - Design and coding required

Number of Pages Required

5+ page

Colors
0054AA
0677BA
7BADD7
CADEEF
E8F1F8

Requirements
Must have
• Design a new modern, clean, website for HVAC mechanical business that uses company logo/colors for branding and recognition. Files attached are just for band and color information. Here is a website design that appeals to me https://www.corvellsupply.example/ A clear description of who we are and what we do An easily-navigated site map An easily-navigated site map for mobile devices Easy-to-find contact information Obvious call to action for service, installs or to schedule estimates about us page Provide a way for potential customers to contact us via text or email provide a way that allows a customer to upload a picture to request a service call or quote.
Nice to have

```html
<!DOCTYPE html>
<html lang="en">
<head>
<meta charset="utf-8">
<title>Pelican HVAC – Heating &amp; Air Conditioning</title>
<link href="https://fonts.googleapis.com/css2?family=Roboto:wght@400;500;700&family=Roboto+Slab:wght@600;700&display=swap" rel="stylesheet">
<style>
:root{
  --brand:#0054AA;
  --brand-mid:#0677BA;
  --brand-soft:#7BADD7;
  --brand-pale:#CADEEF;
  --brand-mist:#E8F1F8;
  --navy:#0d2456;
  --navy-deep:#0b1e4a;
  --ink:#1c2a44;
  --text:#2e3440;
  --muted:#6c7482;
  --grey-band:#e4e8eb;
  --card-grey:#f1f2f4;
  --star:#f5b921;
  --white:#ffffff;
}
*{box-sizing:border-box;margin:0;padding:0}
html,body{width:1200px;height:4065px;overflow:hidden}
body{position:relative;font-family:"Roboto",Arial,sans-serif;color:var(--text);background:var(--white)}
.abs{position:absolute}
.slab{font-family:"Roboto Slab",Georgia,serif;font-weight:700}
.btn{position:absolute;display:flex;align-items:center;justify-content:center;background:var(--brand);color:var(--white);border-radius:30px;font-size:18px;font-weight:500;letter-spacing:.2px}

/* header */
.site-header{position:absolute;left:0;top:0;width:1200px;height:87px;background:var(--white);z-index:5}
.brand{position:absolute;left:100px;top:28px;display:flex;align-items:center;gap:12px;z-index:6}
.brand-dot{width:40px;height:40px;border-radius:50%;background:var(--brand)}
.brand-name{font-family:"Roboto",Arial,sans-serif;font-weight:700;font-size:26px;color:var(--navy);letter-spacing:1px}
.main-nav{position:absolute;left:388px;top:34px;display:flex;gap:34px;font-size:15px;font-weight:500;color:var(--ink)}
.main-nav a{color:inherit;text-decoration:none;position:relative}
.main-nav a.active::after{content:"";position:absolute;left:-4px;right:-4px;top:42px;height:3px;background:var(--brand)}
.nav-contact{left:955px;top:21px;width:145px;height:45px;border-radius:2px;font-size:15px}

/* hero */
.hero{position:absolute;left:0;top:87px;width:1200px;height:800px;overflow:hidden}
.hero-bg{position:absolute;inset:0;background:linear-gradient(180deg,#10306b 0%,#173d7d 45%,#2a4f8c 70%,#12306a 100%)}
.hero-phone{position:absolute;left:950px;top:20px;display:flex;align-items:center;gap:10px;color:var(--white);font-size:18px}
.hero-phone .ico{width:28px;height:28px;border-radius:50%;background:var(--white);display:flex;align-items:center;justify-content:center}
.hero-title{position:absolute;left:133px;top:170px;color:var(--white);font-size:52px;line-height:64px;letter-spacing:1px}
.hero-sub{position:absolute;left:133px;top:316px;color:var(--white);font-size:21px}
.hero-btn{left:196px;top:376px;width:196px;height:46px;font-size:17px;justify-content:flex-start;padding-left:30px;background:var(--brand)}
.hero-btn .arrow{position:absolute;right:4px;top:4px;width:38px;height:38px;border-radius:50%;background:var(--brand-mid);display:flex;align-items:center;justify-content:center}

.booking{position:absolute;left:752px;top:142px;width:309px;height:400px;background:var(--navy-deep);border:3px solid #33507f;border-radius:8px;padding:30px 26px}
.booking h2{color:var(--white);font-size:25px;font-weight:500}
.booking p{color:#d7def0;font-size:13px;line-height:17px;margin-top:8px}
.booking .field{height:36px;background:var(--white);border-radius:2px;margin-top:10px;font-size:12px;color:var(--muted);display:flex;align-items:center;padding-left:16px;position:relative}
.booking .field:first-of-type{margin-top:22px}
.booking .field svg{position:absolute;right:12px;top:13px}
.booking .submit{margin-top:10px;height:42px;background:var(--brand);color:var(--white);display:flex;align-items:center;justify-content:center;font-size:16px;font-weight:500}

.hero-curve{position:absolute;left:0;top:540px}
.van{position:absolute;left:0;top:537px;width:521px;height:330px;border-radius:40px 160px 60px 20px;background:linear-gradient(160deg,#f3f5f8 0%,#cdd4de 55%,#1f5aa8 80%,#9aa4b2 100%);z-index:2}

/* about */
.about-photo{position:absolute;left:100px;top:984px;width:462px;height:346px;border-radius:50%;border:6px solid #d9dde3;background:linear-gradient(135deg,#c66a4a 0%,#3b5fb0 40%,#dfe6ef 100%)}
.section-title{position:absolute;font-size:41px;letter-spacing:.5px;color:var(--navy);white-space:nowrap}
.section-title .accent{color:var(--brand)}
.about-copy{position:absolute;left:640px;top:1026px;width:460px;font-size:19px;line-height:28.5px;color:var(--text)}
.about-copy p+p{margin-top:16px}

/* services */
.services{position:absolute;left:0;top:1472px;width:1200px;height:907px;background:var(--grey-band)}
.svc{position:absolute;width:323px;height:275px;overflow:hidden}
.svc .photo{position:absolute;inset:0}
.svc .label{position:absolute;left:0;right:0;bottom:42px;text-align:center;color:var(--white);font-family:"Roboto Slab",Georgia,serif;font-weight:700;font-size:18px;text-shadow:0 1px 3px rgba(0,0,0,.5)}
.svc.featured .photo{background:linear-gradient(180deg,rgba(13,36,86,.92),rgba(13,36,86,.85)),linear-gradient(135deg,#2d4f8f,#0f2a5e)}
.svc.featured .inner{position:absolute;left:30px;right:30px;top:48px;text-align:center;color:var(--white)}
.svc.featured h3{font-family:"Roboto Slab",Georgia,serif;font-size:18px}
.svc.featured p{font-size:15px;line-height:24px;margin-top:24px}
.svc.featured .mini{display:inline-block;margin-top:14px;padding:9px 26px;border-radius:20px;background:var(--brand);font-size:11px}

/* what we do */
.what{position:absolute;left:0;top:2379px;width:1200px;height:615px;background:linear-gradient(180deg,#0f2a60 0%,#15346f 50%,#1b3b74 100%)}
.what .section-title{color:var(--white)}
.what-copy{position:absolute;left:100px;top:202px;width:460px;font-size:19px;line-height:28.5px;color:#e3e8f3}
.what-copy p+p{margin-top:16px}
.bubble{position:absolute;border-radius:50%;border:4px solid #e1e6ee}

/* reviews */
.review{position:absolute;top:3224px;width:316px;height:213px;border-radius:8px;background:var(--card-grey);padding:66px 34px 0}
.review.featured{background:var(--brand);box-shadow:0 14px 26px rgba(0,40,100,.25)}
.review p{font-size:13.5px;line-height:22px;color:var(--muted)}
.review .who{position:absolute;left:34px;bottom:30px;font-size:13px;color:var(--muted)}
.review .who b{display:block;font-weight:500;color:var(--ink);font-size:14px}
.review .stars{position:absolute;right:40px;bottom:40px;font-size:17px;letter-spacing:3px;color:var(--star)}
.review .stars span{color:#c8ccd3}
.review.featured p,.review.featured .who,.review.featured .who b{color:var(--white)}
.review.featured .stars span{color:#dbe5f3}
.review.featured .rule{position:absolute;left:34px;right:40px;bottom:78px;height:1px;background:rgba(255,255,255,.3)}
.avatar{position:absolute;top:3185px;width:80px;height:80px;border-radius:50%;border:3px solid var(--white);background:linear-gradient(180deg,#b9bfc8,#6e7683)}

/* footer */
.site-footer{position:absolute;left:0;top:3524px;width:1200px;height:541px;background:var(--navy)}
.foot-brand{position:absolute;left:100px;top:80px;display:flex;align-items:center;gap:12px}
.foot-brand .brand-name{color:var(--white)}
.foot-brand .brand-dot{background:var(--white)}
.tagline{position:absolute;left:780px;top:84px;color:var(--white);font-size:27px;line-height:41px;font-weight:500}
.col-head{position:absolute;top:202px;color:var(--white);font-size:17px;font-weight:500}
.vline{position:absolute;top:192px;width:1px;height:225px;background:rgba(255,255,255,.2)}
.ci{position:absolute;left:100px;width:50px;height:50px;border-radius:4px;background:var(--brand);display:flex;align-items:center;justify-content:center}
.ct{position:absolute;left:170px;color:var(--white);font-size:15px;line-height:21px}
.ct span{color:#c6d0e4}
.links{position:absolute;left:474px;top:244px;list-style:none;font-size:14px;color:#c6d0e4}
.links li{height:25.6px;display:flex;align-items:center;gap:10px}
.links li::before{content:"";width:12px;height:12px;border-radius:50%;background:#c6d0e4}
.news-input{position:absolute;left:770px;top:234px;width:326px;height:44px;border-radius:22px;background:#1a3f86;color:#b8c4dc;font-size:14px;display:flex;align-items:center;padding-left:30px}
.news-btn{left:770px;top:292px;width:142px;height:44px;font-size:15px;justify-content:flex-start;padding-left:26px}
.news-btn .arrow{position:absolute;right:4px;top:4px;width:36px;height:36px;border-radius:50%;background:var(--brand-mid);display:flex;align-items:center;justify-content:center}
.hline{position:absolute;left:100px;top:455px;width:1000px;height:1px;background:rgba(255,255,255,.2)}
.legal{position:absolute;top:485px;color:#c6d0e4;font-size:13px}
.social{position:absolute;top:482px;width:26px;height:26px;border-radius:50%;background:var(--white)}
</style>
</head>
<body>

<header class="site-header">
  <div class="brand"><span class="brand-dot"></span><span class="brand-name">PELICAN HVAC</span></div>
  <nav class="main-nav">
    <a class="active">HOME</a><a>OUR SERVICES</a><a>ABOUT US</a><a>TESTIMONIALS</a><a>BLOG</a>
  </nav>
  <a class="btn nav-contact">CONTACT</a>
</header>

<section class="hero">
  <div class="hero-bg" role="img" aria-label="City skyline at dusk beside a river"></div>
  <div class="hero-phone"><span class="ico"><svg width="14" height="14" viewBox="0 0 24 24"><path fill="#0d2456" d="M6.6 10.8a15 15 0 006.6 6.6l2.2-2.2c.3-.3.7-.4 1-.2 1.1.4 2.3.6 3.6.6.6 0 1 .4 1 1V20c0 .6-.4 1-1 1C10.6 21 3 13.4 3 4c0-.6.4-1 1-1h3.5c.6 0 1 .4 1 1 0 1.3.2 2.5.6 3.6.1.3 0 .7-.2 1z"/></svg></span>555 010 4477</div>
  <h1 class="hero-title slab">HEATING &amp; AIR<br>CONDITIONING</h1>
  <p class="hero-sub">Bringing You More Than Just Air</p>
  <a class="btn hero-btn">LEARN MORE<span class="arrow"><svg width="12" height="16" viewBox="0 0 12 16"><path d="M3 2l6 6-6 6" stroke="#fff" stroke-width="2.5" fill="none"/></svg></span></a>

  <form class="booking">
    <h2>Book Our Service</h2>
    <p>We make sure your air conditioning and heating systems.</p>
    <div class="field">Name</div>
    <div class="field">Phone</div>
    <div class="field">Email Address</div>
    <div class="field">Choose Services<svg width="12" height="8" viewBox="0 0 12 8"><path d="M1 1l5 5 5-5" stroke="#555" stroke-width="1.5" fill="none"/></svg></div>
    <div class="submit">SUBMIUT</div>
  </form>

  <svg class="hero-curve" width="1200" height="260" viewBox="0 0 1200 260">
    <path d="M0 250 C300 250 650 210 900 160 C1020 135 1120 100 1200 60 L1200 260 L0 260 Z" fill="#fff"/>
  </svg>
</section>
<div class="van" role="img" aria-label="White service van with blue branding"></div>

<section class="about">
  <div class="about-photo" role="img" aria-label="Technician servicing an outdoor air conditioning unit"></div>
  <h2 class="section-title slab" style="left:640px;top:944px"><span class="accent">ABOUT</span> PELICAN</h2>
  <div class="about-copy">
    <p>Lorem ipsum is simply dummy text of the printing and typesetting industry. Lorem Ipsum has been the industry's standard dummy text ever since the 1500s, when an unknown printer.</p>
    <p>when an unknown printer took a galley of type and scrambled it to make a type specimen book. It has survived not only five centuries, but also the leap into electronic typesetting.</p>
  </div>
  <a class="btn" style="left:641px;top:1307px;width:185px;height:54px">LEARN MORE</a>
</section>

<section class="services">
  <h2 class="section-title slab" style="left:0;width:1200px;text-align:center;top:62px"><span class="accent">OUR</span> SERVICES</h2>

  <div class="svc" style="left:100px;top:170px"><div class="photo" role="img" aria-label="Technicians inspecting an outdoor air conditioner" style="background:linear-gradient(135deg,#e6e9ee,#8ea3c2 55%,#2b4d8c)"></div><div class="label">AIR CONDITIONING</div></div>
  <div class="svc featured" style="left:439px;top:170px"><div class="photo" role="img" aria-label="Technician working on a heating system"></div><div class="inner"><h3>HEATING</h3><p>Lorem ipsum is simply dummy text of the printing and typesetting industry.</p><span class="mini">LEARN MORE</span></div></div>
  <div class="svc" style="left:777px;top:170px"><div class="photo" role="img" aria-label="Hands fitting a gas valve and pressure gauge" style="background:linear-gradient(135deg,#e3d6cf,#b16c5a 45%,#34548f)"></div><div class="label">GAS FITTING</div></div>

  <div class="svc" style="left:100px;top:462px"><div class="photo" role="img" aria-label="Manifold gauges held in front of a condenser" style="background:linear-gradient(135deg,#e9ecef,#9aa6b5 50%,#3a5a92)"></div><div class="label">CONTROLS</div></div>
  <div class="svc" style="left:439px;top:462px"><div class="photo" role="img" aria-label="Heat pump unit beside a wooden fence" style="background:linear-gradient(135deg,#8a8278,#6f7680 50%,#4a4f55)"></div><div class="label">PUMPS</div></div>
  <div class="svc" style="left:777px;top:462px"><div class="photo" role="img" aria-label="Technician installing an indoor unit" style="background:linear-gradient(135deg,#eef0f3,#b9c2cf 50%,#2d4f8e)"></div><div class="label">NEW INSTALL</div></div>

  <a class="btn" style="left:507px;top:775px;width:185px;height:54px">LEARN MORE</a>
</section>

<section class="what" role="img" aria-label="Night city skyline in blue tones behind the section content">
  <h2 class="section-title slab" style="left:100px;top:106px"><span class="accent" style="color:#2f74d0">WHAT</span> WE DO</h2>
  <div class="what-copy">
    <p>Lorem ipsum is simply dummy text of the printing and typesetting industry. Lorem Ipsum has been the industry's standard dummy text ever since the 1500s, when an unknown printer.</p>
    <p>when an unknown printer took a galley of type and scrambled it to make a type specimen book. It has survived not only five centuries, but also the leap into electronic typesetting.</p>
  </div>
  <a class="btn" style="left:103px;top:471px;width:186px;height:52px">LEARN MORE</a>

  <div class="bubble" role="img" aria-label="Technician servicing an outdoor unit" style="left:673px;top:105px;width:289px;height:205px;background:linear-gradient(135deg,#c66a4a,#3b5fb0 45%,#dfe6ef)"></div>
  <div class="bubble" role="img" aria-label="Hands repairing a wall unit" style="left:905px;top:266px;width:191px;height:134px;background:linear-gradient(135deg,#f1f3f6,#c8ced7 60%,#8290a6)"></div>
  <div class="bubble" role="img" aria-label="Outdoor unit against a brick wall" style="left:725px;top:331px;width:183px;height:129px;background:linear-gradient(135deg,#eceef1,#b7bcc4 55%,#a0553d)"></div>
  <div class="bubble" style="left:911px;top:409px;width:96px;height:70px;background:#1f59b8;border-color:#cfd7e3"></div>
</section>

<section class="reviews">
  <h2 class="section-title slab" style="left:100px;top:3087px"><span class="accent">PEOPLE</span> REVIEWS</h2>
  <div class="abs" style="left:493px;top:3116px;width:525px;height:2px;background:#e4e8ee"></div>
  <svg class="abs" style="left:1045px;top:3106px" width="52" height="20" viewBox="0 0 52 20"><path d="M20 10H2M8 4L2 10l6 6" stroke="#9fb3d3" stroke-width="2" fill="none"/><path d="M32 10h18M44 4l6 6-6 6" stroke="#0054AA" stroke-width="2" fill="none"/></svg>

  <article class="review featured" style="left:100px"><p>Lorem Ipsum is simply dummy text of the printing and typesetting industry. Lorem Ipsum has been the industry's.</p><div class="rule"></div><div class="who"><b>Mara Ellis</b>Service technicion</div><div class="stars">★★★★<span>★</span></div></article>
  <article class="review" style="left:442px"><p>Lorem Ipsum is simply dummy text of the printing and typesetting industry. Lorem Ipsum has been the industry's.</p><div class="who"><b>Mara Ellis</b>Service technicion</div><div class="stars">★★★★<span>★</span></div></article>
  <article class="review" style="left:785px"><p>Lorem Ipsum is simply dummy text of the printing and typesetting industry. Lorem Ipsum has been the industry's.</p><div class="who"><b>Mara Ellis</b>Service technicion</div><div class="stars">★★★★<span>★</span></div></article>

  <div class="avatar" role="img" aria-label="Reviewer portrait" style="left:134px"></div>
  <div class="avatar" role="img" aria-label="Reviewer portrait" style="left:476px"></div>
  <div class="avatar" role="img" aria-label="Reviewer portrait" style="left:819px"></div>
</section>

<footer class="site-footer">
  <div class="foot-brand"><span class="brand-dot"></span><span class="brand-name">PELICAN HVAC</span></div>
  <p class="tagline">QUALITY AIR<br>CONDITIONING SERVICE</p>

  <h4 class="col-head" style="left:100px">CONTACT</h4>
  <div class="vline" style="left:393px"></div>
  <div class="ci" style="top:221px"><svg width="24" height="18" viewBox="0 0 24 18"><rect x="1" y="1" width="22" height="16" rx="2" stroke="#fff" stroke-width="1.8" fill="none"/><path d="M1 2l11 8 11-8" stroke="#fff" stroke-width="1.8" fill="none"/></svg></div>
  <div class="ct" style="top:226px">Email:<br><span>hello@pelicanhvac.example</span></div>
  <div class="ci" style="top:313px"><svg width="22" height="22" viewBox="0 0 24 24"><path fill="none" stroke="#fff" stroke-width="1.8" d="M6.6 10.8a15 15 0 006.6 6.6l2.2-2.2c.3-.3.7-.4 1-.2 1.1.4 2.3.6 3.6.6.6 0 1 .4 1 1V20c0 .6-.4 1-1 1C10.6 21 3 13.4 3 4c0-.6.4-1 1-1h3.5c.6 0 1 .4 1 1 0 1.3.2 2.5.6 3.6.1.3 0 .7-.2 1z"/></svg></div>
  <div class="ct" style="top:318px">Call Us:<br><span>555 010 4477</span></div>

  <h4 class="col-head" style="left:474px">LINKS</h4>
  <ul class="links"><li>Home</li><li>About Us</li><li>Services</li><li>Blog</li><li>Sitemap</li><li>Location</li><li>Contact Us</li></ul>

  <h4 class="col-head" style="left:785px">OUR NEWS LETTER</h4>
  <div class="news-input">Enter Your email....</div>
  <a class="btn news-btn">SUBMIT<span class="arrow"><svg width="10" height="14" viewBox="0 0 12 16"><path d="M3 2l6 6-6 6" stroke="#fff" stroke-width="2.5" fill="none"/></svg></span></a>

  <div class="hline"></div>
  <p class="legal" style="left:100px">Copyright @ Pelican 2024</p>
  <p class="legal" style="left:386px">Cookie policy &nbsp;&nbsp;|&nbsp;&nbsp; Terms of Condition</p>
  <span class="social" style="left:992px"></span>
  <span class="social" style="left:1028px"></span>
  <span class="social" style="left:1064px"></span>
</footer>

</body>
</html>
```